Design a Travel and Tourism website

We would like a freelancer to design a website that is essentially easy to use and navigate database providing local information for Travelers about destination countries.

We proposed website would discuss different rates, fees, visa requirement, resort locations, cheap flights, etc. This website should be elegant and modern. Our business name is rovanix.
Some reference websites are zemplorift.ca, brindlefoxhaven.com,
There should be a forum in the website where travell\ers discuss about their first hand tranvel experience to such destinations.

Tourism

```html
<!DOCTYPE html>
<html lang="en">
<head>
<meta charset="utf-8">
<title>rovanix — Travel and Tourism</title>
<link rel="stylesheet" href="https://fonts.googleapis.com/css2?family=Mulish:wght@300;400;600;700&display=swap">
<style>
:root{
  --brand:#1a9ad9;
  --brand-dark:#0f7fb8;
  --orange:#f7941d;
  --orange-dark:#e07400;
  --ink:#222;
  --muted:#8a8a8a;
  --grey-bg:#efefef;
  --footer:#1da7e8;
  --white:#fff;
  --black:#1b1b1b;
}
*{box-sizing:border-box;margin:0;padding:0}
html,body{width:1200px;height:2510px;overflow:hidden}
body{position:relative;font-family:"Mulish",Arial,sans-serif;color:var(--ink);background:var(--white)}

/* header */
.site-header{position:absolute;left:0;top:0;width:1200px;height:90px;background:var(--white)}
.brand{position:absolute;left:125px;top:14px;font-size:42px;font-weight:400;color:var(--brand);letter-spacing:0.5px}
.main-nav a{position:absolute;top:32px;font-size:16px;color:#666;text-decoration:none}
.nav-icon{position:absolute;top:28px}

/* hero */
.hero{position:absolute;left:0;top:90px;width:1200px;height:529px;background:linear-gradient(180deg,#6fa9d8 0%,#a9cde8 40%,#d9b79a 55%,#2f7fb0 72%,#2a6d97 100%)}
.tab{position:absolute;top:298px;height:47px;font-size:19px;text-transform:uppercase;display:flex;align-items:center;justify-content:center;color:var(--orange);background:var(--white)}
.tab.is-active{background:var(--orange-dark);color:var(--white)}
.search-panel{position:absolute;left:125px;top:345px;width:948px;height:109px;background:var(--orange)}
.field-label{position:absolute;top:362px;font-size:16px;color:var(--white)}
.field{position:absolute;top:388px;height:39px;background:var(--white);font-size:12px;color:#888;display:flex;align-items:center;gap:8px;padding-left:12px}
.search-btn{position:absolute;left:937px;top:388px;width:116px;height:39px;background:var(--black);color:var(--white);font-size:18px;display:flex;align-items:center;justify-content:center}
.dots{position:absolute;left:552px;top:582px;display:flex;gap:8px}
.dots span{width:14px;height:14px;border-radius:50%;background:var(--white)}
.dots span.is-current{background:transparent;border:2px solid var(--white)}

/* welcome */
.welcome-title{position:absolute;left:125px;top:692px;font-size:37px;font-weight:400;color:var(--ink)}
.welcome-text{position:absolute;left:127px;top:760px;width:480px;font-size:13.5px;line-height:28px;color:var(--muted)}
.btn-primary{position:absolute;left:127px;top:889px;width:132px;height:38px;background:var(--brand);color:var(--white);font-size:16px;display:flex;align-items:center;justify-content:center}
.welcome-art{position:absolute;left:650px;top:640px;width:350px;height:370px;border-radius:6px;background:linear-gradient(160deg,#7cc4ea 0%,#9fd3ee 35%,#6aa860 60%,#e8dcc0 75%,#d8443a 100%)}

/* destinations */
.destinations{position:absolute;left:0;top:1013px;width:1200px;height:488px;background:var(--grey-bg)}
.section-title{position:absolute;font-size:30px;font-weight:400;color:var(--brand)}
.card{position:absolute;top:1135px;width:303px;height:310px;background:var(--white);box-shadow:0 1px 4px rgba(0,0,0,.18)}
.card-photo{width:303px;height:184px}
.card-title{position:absolute;left:23px;top:212px;font-size:18px;color:#333}
.card-text{position:absolute;left:23px;top:241px;font-size:11px;color:#777}
.price-old{position:absolute;left:27px;top:268px;font-size:18px;color:#444;text-decoration:line-through}
.price-new{position:absolute;left:78px;top:262px;font-size:27px;color:var(--orange)}
.stars{position:absolute;right:20px;top:268px;font-size:18px;color:var(--orange);letter-spacing:1px}

/* categories */
.tile{position:absolute;top:1547px;width:238px;height:217px;display:flex;flex-direction:column;align-items:center;justify-content:center;gap:14px;color:var(--white);font-size:19px;font-weight:600;text-transform:uppercase}
.tile-tours{background:linear-gradient(180deg,#7aa7c8,#c9b79a)}
.tile-resorts{background:linear-gradient(180deg,#3f6a52,#1f5f86)}
.tile-flights{background:linear-gradient(180deg,#1d3f66,#4f7ea6)}
.tile-visa{background:linear-gradient(180deg,#5a4c3e,#2f3b48)}
.arrow{position:absolute;top:1625px}

/* info links */
.link-col{position:absolute;top:1905px;list-style:none}
.link-col li{height:38.5px;font-size:14px;color:#888;display:flex;align-items:flex-start;gap:10px}
.link-col li::before{content:"";width:0;height:0;margin-top:3px;border-left:6px solid #aaa;border-top:5px solid transparent;border-bottom:5px solid transparent}

/* footer */
.site-footer{position:absolute;left:0;top:2142px;width:1200px;height:368px;background:var(--footer)}
.footer-heading{position:absolute;top:2194px;font-size:18px;font-weight:600;text-transform:uppercase;color:var(--white)}
.footer-links{position:absolute;top:2234px;list-style:none;color:var(--white)}
.footer-links li{height:26px;font-size:15px;font-weight:300}
.newsletter-input{position:absolute;left:867px;top:2233px;width:224px;height:35px;background:var(--white);color:#bbb;font-size:12px;display:flex;align-items:center;gap:8px;padding-left:12px}
.subscribe-btn{position:absolute;left:867px;top:2276px;width:111px;height:36px;background:var(--brand-dark);color:var(--white);font-size:15px;font-weight:600;display:flex;align-items:center;justify-content:center}
.social{position:absolute;top:2333px;width:34px;height:34px;border-radius:50%;background:var(--white)}
.footer-rule{position:absolute;left:141px;top:2440px;width:939px;height:1px;background:rgba(255,255,255,.6)}
.copyright{position:absolute;left:0;top:2466px;width:1200px;text-align:center;font-size:13px;font-weight:300;color:var(--white)}
</style>
</head>
<body>

<header class="site-header">
  <div class="brand">rovanix</div>
  <nav class="main-nav">
    <a style="left:490px">About</a>
    <a style="left:571px">Flights</a>
    <a style="left:654px">Hotel</a>
    <a style="left:728px">Visa</a>
    <a style="left:792px">Tours</a>
    <a style="left:867px">Support</a>
  </nav>
  <svg class="nav-icon" style="left:967px" width="22" height="24" viewBox="0 0 22 24"><circle cx="11" cy="7" r="6" fill="#1a9ad9"/><path d="M0 24c0-7 5-10 11-10s11 3 11 10z" fill="#1a9ad9"/></svg>
  <svg class="nav-icon" style="left:1018px" width="26" height="24" viewBox="0 0 26 24"><path d="M15 2h8v20h-8" fill="none" stroke="#1a9ad9" stroke-width="3"/><path d="M1 10h9V5l8 7-8 7v-5H1z" fill="#1a9ad9"/></svg>
</header>

<section class="hero" role="img" aria-label="Smiling family on a sunny beach with the sea behind them"></section>
<div class="tab is-active" style="left:125px;width:148px">Holiday</div>
<div class="tab" style="left:276px;width:148px">Flights</div>
<div class="tab" style="left:435px;width:147px">Hotels</div>
<div class="tab" style="left:594px;width:144px">Other</div>
<div class="search-panel"></div>
<div class="field-label" style="left:156px">Find Tour</div>
<div class="field-label" style="left:412px">Location</div>
<div class="field-label" style="left:644px">Depart</div>
<div class="field-label" style="left:793px">Arrival</div>
<div class="field" style="left:156px;width:247px"><svg width="14" height="14" viewBox="0 0 14 14"><circle cx="6" cy="6" r="4.5" fill="none" stroke="#999" stroke-width="2"/><path d="M9 9l4 4" stroke="#999" stroke-width="2"/></svg>Tour Tittle here</div>
<div class="field" style="left:415px;width:218px"><svg width="12" height="15" viewBox="0 0 12 15"><path d="M6 0a6 6 0 0 0-6 6c0 4 6 9 6 9s6-5 6-9a6 6 0 0 0-6-6z" fill="#999"/><circle cx="6" cy="6" r="2" fill="#fff"/></svg>City Destnation</div>
<div class="field" style="left:639px;width:141px"><svg width="15" height="15" viewBox="0 0 15 15"><rect x="1" y="2" width="13" height="12" fill="none" stroke="#999" stroke-width="1.5"/><path d="M1 6h13M4 0v4M11 0v4" stroke="#999" stroke-width="1.5"/></svg>02/11/17</div>
<div class="field" style="left:790px;width:139px"><svg width="15" height="15" viewBox="0 0 15 15"><rect x="1" y="2" width="13" height="12" fill="none" stroke="#999" stroke-width="1.5"/><path d="M1 6h13M4 0v4M11 0v4" stroke="#999" stroke-width="1.5"/></svg>10/11/17</div>
<div class="search-btn">Search</div>
<div class="dots"><span class="is-current"></span><span></span><span></span><span></span></div>

<section class="welcome">
  <h1 class="welcome-title">Welcome to Our Website</h1>
  <p class="welcome-text">Praesent elementum elit at tellus nec ultricies sit amet porttitor mattis enim In massa libero interdum nec interdum vel blandit sed nulla In ullamcorper est eget tempor cursus neque mi consectetuer mi a ultricies massa est sed nisl Class aptent taciti sociosqu ad litora to</p>
  <div class="btn-primary">Read More</div>
  <div class="welcome-art" role="img" aria-label="Open red suitcase holding a tiny beach with palm trees and sun loungers"></div>
</section>

<section class="destinations"></section>
<h2 class="section-title" style="left:130px;top:1080px">Top Destinations</h2>

<article class="card" style="left:129px">
  <div class="card-photo" role="img" aria-label="Beach with a thatched umbrella and sun loungers" style="background:linear-gradient(180deg,#4a9ad6 0%,#9fd0ee 45%,#e2cfa6 60%,#c8a878 100%)"></div>
  <div class="card-title">Tour Tittle here</div>
  <div class="card-text">per inceptos hymenaeos Proin nulla arcu</div>
  <div class="price-old">$229</div><div class="price-new">$175</div>
  <div class="stars">★★★★</div>
</article>
<article class="card" style="left:445px">
  <div class="card-photo" role="img" aria-label="Stone bridge over a calm river with a castle on the hill" style="background:linear-gradient(180deg,#b9c7d6 0%,#6f8f4e 45%,#c9b48a 58%,#5d7a52 80%,#3f5a3c 100%)"></div>
  <div class="card-title">Tour Tittle here</div>
  <div class="card-text">per inceptos hymenaeos Proin nulla arcu</div>
  <div class="price-old">$229</div><div class="price-new">$175</div>
  <div class="stars">★★★★</div>
</article>
<article class="card" style="left:763px">
  <div class="card-photo" role="img" aria-label="Resort pool surrounded by palm trees and parasols" style="background:linear-gradient(180deg,#5b8a4a 0%,#8fae6a 35%,#d9d2c0 55%,#2bb0d6 70%,#1490bf 100%)"></div>
  <div class="card-title">Tour Tittle here</div>
  <div class="card-text">per inceptos hymenaeos Proin nulla arcu</div>
  <div class="price-old">$229</div><div class="price-new">$175</div>
  <div class="stars">★★★★</div>
</article>

<svg class="arrow" style="left:88px" width="24" height="60" viewBox="0 0 24 60"><path d="M22 2L3 30l19 28" fill="none" stroke="#999" stroke-width="2"/></svg>
<div class="tile tile-tours" style="left:132px" aria-label="Family walking on the beach">
  <svg width="56" height="50" viewBox="0 0 56 50"><path d="M4 26a24 20 0 0 1 48 0z" fill="#fff"/><path d="M28 26v20" stroke="#fff" stroke-width="3"/><path d="M10 48h36" stroke="#fff" stroke-width="3"/></svg>
  <span>Latest Tours</span>
</div>
<div class="tile tile-resorts" style="left:370px" aria-label="Resort pool at dusk">
  <svg width="56" height="56" viewBox="0 0 56 56"><path d="M28 20c-3 12-3 24-6 34h6c2-10 2-22 0-34z" fill="#fff"/><path d="M28 20C20 8 8 10 4 18c8-4 16-2 24 2zM28 20c8-12 20-10 24-2-8-4-16-2-24 2zM28 20C24 8 30 2 38 2c-6 4-8 10-10 18z" fill="#fff"/></svg>
  <span>Top Resorts</span>
</div>
<div class="tile tile-flights" style="left:608px" aria-label="Aeroplane in a blue sky">
  <svg width="56" height="56" viewBox="0 0 56 56"><path d="M50 4c3 3-2 9-6 13l3 25-4 4-9-19-9 9 1 8-3 3-4-9-9-4 3-3 8 1 9-9L11 14l4-4 25 3c4-4 10-9 10-9z" fill="#fff"/></svg>
  <span>Cheap Flights</span>
</div>
<div class="tile tile-visa" style="left:846px" aria-label="Passport and travel documents on a map">
  <svg width="64" height="44" viewBox="0 0 64 44"><rect x="3" y="3" width="58" height="38" rx="3" fill="none" stroke="#fff" stroke-width="3"/><path d="M14 22h36" stroke="#fff" stroke-width="4"/></svg>
  <span>Visa &amp; Other</span>
</div>
<svg class="arrow" style="left:1098px" width="24" height="60" viewBox="0 0 24 60"><path d="M2 2l19 28L2 58" fill="none" stroke="#999" stroke-width="2"/></svg>

<h2 class="section-title" style="left:136px;top:1838px;font-size:25px">Check Out More Information</h2>
<ul class="link-col" style="left:141px"><li>Praesent elementum</li><li>Elit at tellus nec ultricies</li><li>Porttitor mattis enim</li><li>Massa libero interdum</li></ul>
<ul class="link-col" style="left:417px"><li>Donec dictum lectus</li><li>Non odio</li><li>Cras a ante</li><li>Vitae enim iaculis</li></ul>
<ul class="link-col" style="left:639px"><li>Dignissim congue leo</li><li>Elit at tellus nec</li><li>Porttitor mattis enim</li><li>Massa libero int</li></ul>
<ul class="link-col" style="left:897px"><li>Duis quam Nam</li><li>Eget lacus</li><li>Aliquam erat</li><li>Volutpat Quisque</li></ul>

<footer class="site-footer"></footer>
<div class="footer-heading" style="left:131px">Quick Links</div>
<div class="footer-heading" style="left:316px">Tours &amp; Hotel</div>
<div class="footer-heading" style="left:534px">Resources</div>
<div class="footer-heading" style="left:720px">Support</div>
<div class="footer-heading" style="left:867px">Join Newsletters</div>
<ul class="footer-links" style="left:133px"><li>About Us</li><li>Our Tours</li><li>Gallery</li><li>Reviews</li><li>Term of Use</li></ul>
<ul class="footer-links" style="left:319px"><li>Kumarakom Hotels</li><li>Lucknow Hotels</li><li>Ludhiana Hotels</li><li>Maharashtra Hotels</li><li>Mumbai Hotels</li></ul>
<ul class="footer-links" style="left:536px"><li>Privacy Policy</li><li>FAQ</li><li>Contact Us</li><li>Newsletters</li></ul>
<ul class="footer-links" style="left:720px"><li>Support</li><li>Career</li><li>Advertise</li><li>Blogs</li></ul>
<div class="newsletter-input"><svg width="14" height="11" viewBox="0 0 14 11"><rect width="14" height="11" fill="#bbb"/><path d="M0 0l7 6 7-6" fill="none" stroke="#fff" stroke-width="1.5"/></svg>Email address</div>
<div class="subscribe-btn">Subscribe</div>
<div class="social" style="left:868px"></div>
<div class="social" style="left:914px"></div>
<div class="social" style="left:960px"></div>
<div class="social" style="left:1007px"></div>
<div class="footer-rule"></div>
<div class="copyright">© 2017 Company Name&nbsp; All right reserved</div>

</body>
</html>
```